Cover für Gedichtbuch
Zielgruppe
Das Buch soll jungen und alten Menschen gefallen. Zielgruppe sind aber vor allem junge Leser zwischen 18 und Mitte 20.
Aufgabenstellung
Für das Erstlingswerk von zwei Nachwuchsautoren wird ein Wendecover gesucht. Sprich: Auf der einen Seite stehen Gedichte mit hellen Gedichten (Liebe, Freude, Glück) - die andere Hälfte besteht aus dunklen Gedichten (Tod, Depression). Das Buch soll gedreht werden. Daher sollen die beiden Coverseiten einen Kontrast darstellen.

```html
<!DOCTYPE html>
<html lang="de">
<head>
<meta charset="utf-8">
<title>Gedichte – Wendecover dunkle / helle</title>
<link rel="stylesheet" href="https://fonts.googleapis.com/css2?family=Cormorant+Garamond:wght@500;600&display=swap">
<style>
  :root {
    --ink: #000000;
    --paper: #ffffff;
    --mist: #d2d2d2;
    --shade: #161616;
    --silver: #dcdcdc;
    --silver-edge: #777777;
  }
  html, body {
    margin: 0;
    padding: 0;
    overflow: hidden;
    background: var(--paper);
  }
  .cover-spread {
    position: relative;
    width: 1200px;
    height: 845px;
    overflow: hidden;
    background: var(--paper);
    font-family: "Cormorant Garamond", Georgia, serif;
  }

  /* dunkle Seite */
  .cover-dark {
    position: absolute;
    left: 0; top: 0;
    width: 593px; height: 845px;
    overflow: hidden;
    background: linear-gradient(to bottom,
      var(--ink) 0%, var(--ink) 9%, #3c3c3c 15%, #e8e8e8 22%,
      var(--paper) 32%, #f2f2f2 62%, #a8a8a8 80%, #3a3a3a 92%, var(--ink) 100%);
  }
  .cover-dark .artwork {
    position: absolute;
    inset: 0;
    background:
      radial-gradient(ellipse 16% 40% at 43% 88%, rgba(0, 0, 0, 0.5), rgba(0, 0, 0, 0) 75%),
      radial-gradient(ellipse 55% 30% at 42% 42%, rgba(70, 70, 70, 0.32), rgba(70, 70, 70, 0) 80%),
      radial-gradient(ellipse 70% 22% at 50% 24%, rgba(90, 90, 90, 0.22), rgba(90, 90, 90, 0) 80%),
      radial-gradient(ellipse 70% 20% at 45% 66%, rgba(60, 60, 60, 0.25), rgba(60, 60, 60, 0) 80%);
  }

  /* helle Seite */
  .cover-light {
    position: absolute;
    left: 606px; top: 0;
    width: 594px; height: 845px;
    overflow: hidden;
    background:
      radial-gradient(ellipse 45% 14% at 95% 20%, rgba(0, 0, 0, 0.9), rgba(0, 0, 0, 0) 80%),
      linear-gradient(to bottom,
        var(--paper) 0%, var(--paper) 10%, #9a9a9a 16%, #2a2a2a 22%,
        var(--shade) 40%, var(--shade) 70%, var(--ink) 75%, #8a8a8a 82%,
        #e6e6e6 90%, var(--paper) 100%);
  }
  .cover-light .artwork {
    position: absolute;
    left: 0; top: 140px;
    width: 594px; height: 510px;
    background:
      radial-gradient(ellipse 60% 40% at 40% 50%, #dadada, rgba(210, 210, 210, 0) 90%),
      linear-gradient(to bottom, #c6c6c6, var(--mist) 50%, #c2c2c2);
    -webkit-mask-image: linear-gradient(to bottom, transparent 0%, #000 14%, #000 86%, transparent 100%);
    mask-image: linear-gradient(to bottom, transparent 0%, #000 14%, #000 86%, transparent 100%);
  }

  /* Typografie */
  .label {
    position: absolute;
    margin: 0;
    font-weight: 500;
    line-height: 1;
    white-space: nowrap;
  }
  .label-dark {
    left: 30px; top: -10px;
    font-size: 186px;
    letter-spacing: 1px;
    color: var(--silver);
    text-shadow:
      1px 1px 0 var(--silver-edge),
      2px 3px 4px rgba(0, 0, 0, 0.6),
      -1px -1px 0 rgba(255, 255, 255, 0.8);
  }
  .title-main {
    left: 150px; top: 318px;
    font-size: 250px;
    font-weight: 600;
    letter-spacing: 6px;
    transform: rotate(180deg);
    color: var(--paper);
    text-shadow:
      -2px -2px 0 var(--silver-edge),
      -4px -5px 7px rgba(0, 0, 0, 0.6);
  }
  .label-light {
    left: 674px; top: 590px;
    font-size: 262px;
    letter-spacing: 3px;
    transform: rotate(180deg);
    color: var(--paper);
    text-shadow:
      -2px -2px 0 #9a9a9a,
      -4px -5px 6px rgba(0, 0, 0, 0.45);
  }
</style>
</head>
<body>
  <main class="cover-spread">
    <section class="cover-dark">
      <div class="artwork" role="img" aria-label="Alte Handschrift mit kahlem Baum als Hintergrund"></div>
    </section>
    <section class="cover-light">
      <div class="artwork" role="img" aria-label="Handschrift in heller Laubsilhouette mit Turmspitze"></div>
    </section>
    <p class="label label-dark">dunkle</p>
    <h1 class="label title-main">Gedichte</h1>
    <p class="label label-light">helle</p>
  </main>
</body>
</html>
```